Travel Agency Website - Simple General

Need a 7 page simple design that is pretty repetitive. Need to be able to load quickly that is SEO optimized. Trying to give ideas on what they can do, be personal as we are local, but at the same time come across as professional and get information easily with little burden.

- Landing Page
- Brimwell Vacations Page
- Family Trips
- Road Trips from Texas
- Other Destinations
- About Us Page
- Contact Us Page

Target Market(s)

Families

Coding

Coded - Design and coding required

Number of Pages Required

5+ page

Colors

Designer to choose colors to be used in the design.

Requirements
Must have
• Like it to flow easily with our logo. Use that for colors, etc.

```html
<!DOCTYPE html>
<html lang="en">
<head>
<meta charset="utf-8">
<title>Roam Together Travel Co.</title>
<link href="https://fonts.googleapis.com/css2?family=Inter:wght@400;500;700&display=swap" rel="stylesheet">
<style>
:root{
  --teal:#2e8585;
  --teal-dark:#1f5d6b;
  --gold:#9b7a3a;
  --ink:#1d1d1d;
  --muted:#6a6a6a;
  --line:#dedede;
  --band:#d9d9d9;
  --white:#ffffff;
}
*{margin:0;padding:0;box-sizing:border-box}
html,body{width:924px;height:1200px;overflow:hidden;background:var(--white);font-family:"Inter",sans-serif;color:var(--ink)}
.page{position:relative;width:924px;height:1200px}
.brand{position:absolute;display:flex;align-items:center;gap:7px;color:var(--teal-dark);font-weight:700;font-size:13px;line-height:1.15}
.brand-dot{width:12px;height:12px;border-radius:50%;background:var(--teal);flex:none}
.brand--header{left:16px;top:27px;width:96px}
.brand--footer{left:115px;top:1115px;width:90px}
.nav{position:absolute;left:202px;top:30px;width:709px;height:39px;background:var(--teal);border:1px solid #25706f;border-radius:7px;display:flex;align-items:center;justify-content:center;gap:24.5px}
.nav a{color:var(--white);text-decoration:none;font-size:10.5px;font-weight:500;white-space:nowrap}
.hero{position:absolute;left:17px;top:98px;width:894px;height:366px;border-radius:10px;overflow:hidden;
  background:linear-gradient(90deg,#a9b3b4 0%,#b7b4ab 35%,#c8b7ab 55%,#a9ab9f 80%,#8c9287 100%)}
.hero-band{position:absolute;left:150px;top:232px;width:630px;height:120px;border-radius:60px;background:rgba(255,255,255,.82)}
.hero-title{position:absolute;left:0;right:0;top:256px;text-align:center;color:var(--teal-dark);font-weight:400;font-size:30.5px;line-height:37px}
.hero-title strong{color:var(--gold);font-weight:700}
.card{position:absolute;width:340px;height:225px;border-radius:7px;overflow:hidden}
.card-label{position:absolute;left:12px;right:12px;bottom:12px;height:32px;border-radius:3px;background:rgba(255,255,255,.78);display:flex;align-items:center;justify-content:center;text-align:center;font-size:11.5px;line-height:12.5px;text-transform:uppercase}
.card--brimwell{left:117px;top:508px;background:linear-gradient(180deg,#3f8ee6 0%,#63a8e8 38%,#4f8a5a 62%,#5b6470 100%)}
.card--family{left:477px;top:509px;height:226px;background:linear-gradient(180deg,#cfe3e6 0%,#b9d1b0 45%,#cdb9aa 100%)}
.card--texas{left:117px;top:754px;height:227px;background:linear-gradient(180deg,#9cc6e8 0%,#f0d6a6 40%,#a98a6a 62%,#8a9692 100%)}
.card--texas .card-label{height:42px;bottom:14px}
.card--other{left:477px;top:754px;height:227px;background:linear-gradient(180deg,#6fb0e8 0%,#a4d0f0 60%,#8fae7a 85%,#b8474c 100%)}
.divider{position:absolute;left:0;top:1025px;width:924px;height:1px;background:var(--line)}
.social{position:absolute;left:113px;top:1060px;display:flex;gap:11px}
.social span{width:16px;height:16px;border-radius:50%;border:1.5px solid var(--ink)}
.vsep{position:absolute;top:1055px;width:1px;height:113px;background:var(--line)}
.contact-row{position:absolute;display:flex;align-items:center;gap:9px;white-space:nowrap;font-size:10px}
.foot-col{position:absolute;top:1061px;font-size:10.5px}
.foot-col h3{font-weight:400;font-size:10.5px;margin-bottom:11px}
.foot-col a{display:block;color:var(--muted);text-decoration:none;margin-bottom:10.5px}
.band{position:absolute;left:0;top:1184px;width:924px;height:16px;background:var(--band)}
</style>
</head>
<body>
<div class="page">
  <div class="brand brand--header"><span class="brand-dot"></span>Roam Together Travel Co.</div>
  <nav class="nav">
    <a href="#">Home</a><a href="#">Brimwell Vacations</a><a href="#">Family Trips</a><a href="#">Road Trips from Texas</a><a href="#">Other Destinations</a><a href="#">About Us</a><a href="#">Contact Us</a>
  </nav>

  <section class="hero" role="img" aria-label="Photo of three friends reading a map in front of an off-road vehicle">
    <div class="hero-band"></div>
    <h1 class="hero-title">Roam Together Travel Co.<br>Your local Guide to <strong>Big Adventure</strong></h1>
  </section>

  <a class="card card--brimwell" role="img" aria-label="Photo of a theme park entrance gate with visitors">
    <span class="card-label">Brimwell Vacations – Land and Sea</span></a>
  <a class="card card--family" role="img" aria-label="Photo of a family walking with luggage at a resort">
    <span class="card-label">Family Trips</span></a>
  <a class="card card--texas" role="img" aria-label="Photo of a Texas city skyline at sunset">
    <span class="card-label">Texas Road Trips<br>(Partnership with Piney Road Van Rentals)</span></a>
  <a class="card card--other" role="img" aria-label="Photo of a suitcase and straw hat with a plane in the sky">
    <span class="card-label">Other Destinations</span></a>

  <div class="divider"></div>

  <footer>
    <div class="social" aria-label="Social links"><span></span><span></span><span></span><span></span></div>
    <div class="brand brand--footer"><span class="brand-dot"></span>Roam Together Travel Co.</div>
    <div class="vsep" style="left:226px"></div>
    <div class="vsep" style="left:453px"></div>
    <div class="vsep" style="left:613px"></div>
    <div class="contact-row" style="left:268px;top:1064px">hello@roamtogethertravel.com</div>
    <div class="contact-row" style="left:243px;top:1095px">
      <svg width="15" height="15" viewBox="0 0 24 24" fill="none" stroke="#777" stroke-width="1.4"><path d="M5 3h4l2 5-3 2a12 12 0 0 0 6 6l2-3 5 2v4a2 2 0 0 1-2 2A17 17 0 0 1 3 5a2 2 0 0 1 2-2z"/></svg>
      555.010.2040</div>
    <div class="foot-col" style="left:477px">
      <h3>Links</h3><a href="#">Home</a><a href="#">About Us</a><a href="#">Contact Us</a>
    </div>
    <div class="foot-col" style="left:672px">
      <h3>Resources</h3><a href="#">Brimwell Vacations</a><a href="#">Family Trips</a><a href="#">Road Trips from Texas</a><a href="#">Other Destinations</a>
    </div>
  </footer>
  <div class="band"></div>
</div>
</body>
</html>
```